BRANDEMEIER & BRANDEMEIER,LLP NEEDS A NEW LETTERHEAD DESIGN

a conservative yet contemporary layout befitting a long established
firm, consistent with the times, some form of logo so it catches ones attention, and is
admirable, but portrays integrity
Updates

I would like to approve #22066987 Please advise how to do this as it’s confusing on the site so I can approve payment for the designer

Target Market(s)

real estate investors and building management people

Industry/Entity Type

Law Firm

Font styles to use
Serif

Colors

Designer to choose colors to be used in the design.

Requirements
Must have
• some form of conservative logo

```html
<!DOCTYPE html>
<html lang="en">
<head>
<meta charset="utf-8">
<title>Brandemeier &amp; Brandemeier Letterhead</title>
<link rel="stylesheet" href="https://fonts.googleapis.com/css2?family=Questrial&family=Didact+Gothic&display=swap">
<style>
  :root {
    --backdrop: #cbccd1;
    --paper: #f2f2f2;
    --ink: #8a8c94;
    --ink-strong: #7f818a;
    --rule: #a9abb1;
  }
  * { margin: 0; padding: 0; box-sizing: border-box; }
  html, body {
    width: 1200px;
    height: 1166px;
    overflow: hidden;
    background: var(--backdrop);
  }
  .letterhead {
    position: absolute;
    left: 173px;
    top: 33px;
    width: 853px;
    height: 1100px;
    background: var(--paper);
    color: var(--ink);
    font-family: "Didact Gothic", "Questrial", sans-serif;
  }
  .brand {
    position: absolute;
    left: 55px;
    top: 66px;
    display: flex;
    align-items: center;
    gap: 13px;
  }
  .brand-mark {
    width: 50px;
    height: 50px;
    border-radius: 50%;
    background: var(--ink-strong);
    flex: none;
  }
  .brand-name {
    font-family: "Questrial", sans-serif;
    font-size: 20.5px;
    line-height: 23px;
    letter-spacing: 0.9px;
    color: var(--ink-strong);
    text-transform: uppercase;
  }
  .tagline {
    position: absolute;
    right: 55px;
    top: 69px;
    font-size: 13px;
    letter-spacing: 0.3px;
    text-transform: uppercase;
    padding-bottom: 4px;
    border-bottom: 1px solid var(--rule);
  }
  .footer {
    position: absolute;
    left: 55px;
    right: 55px;
    top: 1026px;
    border-top: 1px solid var(--rule);
    padding-top: 12px;
    display: flex;
    justify-content: space-between;
    align-items: flex-start;
    font-size: 8.6px;
    letter-spacing: 0.3px;
    text-transform: uppercase;
  }
  .footer-details p { line-height: 12px; }
  .footer-web {
    letter-spacing: 3.2px;
    font-size: 8.6px;
    line-height: 12px;
    color: var(--ink-strong);
  }
</style>
</head>
<body>
  <main class="letterhead">
    <header>
      <div class="brand">
        <div class="brand-mark" aria-hidden="true"></div>
        <div class="brand-name">Brandemeier<br>&amp; Brandemeier</div>
      </div>
      <div class="tagline">Attorneys and Counselors at Law</div>
    </header>
    <footer class="footer">
      <div class="footer-details">
        <p>Brandemeier &amp; Brandemeier, LLP · 118 Harbor Street Suite 210, Brooklyn, New York 11201</p>
        <p>Phone: (718) 555-0142 · Fax: (718)-555-0178 · Email: info@bbrelaw.com</p>
      </div>
      <div class="footer-web">www.bbrelaw.com</div>
    </footer>
  </main>
</body>
</html>
```